Website for Boutique Property Consultancy in UK

We are looking to designing a website for our Property Consultancy Services that follows a minimalistic clean style that is also bold and intriguing.
The website will be based on one landing page and a link to plain circle link Page and email link.

Dominant features will be the company logo or icon and colours.

Brand colours provided for guidance.

Looking to achieve a minimalistic clean style that is also bold and intriguing.

"Updated"
Page 1 - Landing Page with the Hyperlinks to Pick a Service, Training Portal and Quill Meadow Portal. example landing page https://brantwistle.co.uk/

Page 2 - Shows all the Services and Sectors

Target Market(s)

Occupier Clients, Tech Companies, Property Developers, Infrastructure Clients and Major Consultants

Industry/Entity Type

Construction

Coding

Coded - Design and coding required

Number of Pages Required

2 page

Font styles to use
Other font styles liked:
• Century Gothic or Futuris (Headings)

Colors
0054AA
0677BA
7BADD7
CADEEF
E8F1F8
00AB8E
00BBA5
67D7C9
C6EFE9
E9F9F6

Requirements
Must have
• Company Logo, link to enquiry and plain circle link

```html
<!DOCTYPE html>
<html lang="en">
<head>
<meta charset="utf-8">
<title>Ferrow Lane — Pick a Service</title>
<link href="https://fonts.googleapis.com/css2?family=Questrial&display=swap" rel="stylesheet">
<style>
  :root {
    --green: #1ec075;
    --ink: #1e1e1e;
    --mist: #e9e9eb;
    --white: #ffffff;
    --text-soft: #d6d6d6;
    --rule: #2e2e2e;
    --photo-light: #b8b8b8;
    --photo-dark: #3a3a3a;
  }
  * { margin: 0; padding: 0; box-sizing: border-box; }
  html, body { width: 888px; height: 1200px; overflow: hidden; }
  body {
    background: var(--mist);
    font-family: "Questrial", "Century Gothic", sans-serif;
    position: relative;
  }
  .page {
    position: absolute;
    left: 0; top: 322px;
    width: 888px; height: 555px;
    background: var(--ink);
    overflow: hidden;
  }
  .hero-photo {
    position: absolute;
    left: 0; top: 0;
    width: 342px; height: 555px;
    background: linear-gradient(150deg, var(--photo-dark) 0%, #6e6e6e 35%, var(--photo-light) 62%, #8a8a8a 80%, var(--photo-dark) 100%);
  }
  .site-header {
    position: absolute;
    left: 0; top: 0;
    width: 888px; height: 48px;
    border-bottom: 1px solid rgba(255,255,255,0.06);
  }
  .brand {
    position: absolute;
    left: 55px; top: 14px;
    font-size: 15px;
    color: var(--white);
    letter-spacing: 0.3px;
  }
  .main-nav a {
    position: absolute;
    top: 18px;
    font-size: 8.5px;
    color: var(--white);
    text-decoration: none;
    white-space: nowrap;
  }
  .main-nav a.is-active { color: var(--green); }
  .nav-services { left: 568px; }
  .nav-training { left: 654px; }
  .nav-portal { left: 738px; }
  .social-link {
    position: absolute;
    left: 807px; top: 10px;
    width: 26px; height: 26px;
    border-radius: 50%;
    background: var(--green);
  }
  .section-title {
    position: absolute;
    left: 396px;
    font-size: 16.5px;
    font-weight: 400;
    color: var(--white);
  }
  .services-title { top: 101px; }
  .sector-title { top: 437px; }
  .service-tabs {
    position: absolute;
    left: 396px; top: 140px;
    height: 25px;
  }
  .tab {
    position: absolute;
    top: 0; height: 25px;
    line-height: 25px;
    font-size: 7.8px;
    color: var(--white);
    white-space: nowrap;
  }
  .tab.is-active {
    border: 1px solid var(--green);
    padding: 0 7px;
    line-height: 23px;
  }
  .tab-pre { left: 0; }
  .tab-post { left: 108px; }
  .tab-claims { left: 202px; }
  .tab-training { left: 317px; }
  .bullet-list {
    position: absolute;
    left: 399px;
    list-style: none;
  }
  .bullet-list li {
    position: relative;
    padding-left: 8px;
    height: 20.5px;
    font-size: 9.3px;
    color: var(--text-soft);
    white-space: nowrap;
  }
  .bullet-list li::before {
    content: "";
    position: absolute;
    left: 0; top: 4px;
    width: 3.5px; height: 3.5px;
    border-radius: 50%;
    background: var(--green);
  }
  .service-list { top: 185px; }
  .sector-list { top: 470px; }
  .section-rule {
    position: absolute;
    left: 396px; top: 400px;
    width: 436px; height: 1px;
    background: var(--rule);
  }
</style>
</head>
<body>
  <main class="page">
    <div class="hero-photo" role="img" aria-label="Black and white photo of hands signing a contract with a pen"></div>

    <header class="site-header">
      <div class="brand">Ferrow Lane</div>
      <nav class="main-nav">
        <a class="nav-services is-active" href="#services">+ Pick a Service</a>
        <a class="nav-training" href="#training">+ Training Portal</a>
        <a class="nav-portal" href="#portal">+ Quill Meadow</a>
      </nav>
      <a class="social-link" href="#social" aria-label="Company social profile"></a>
    </header>

    <h2 class="section-title services-title">Pick a Service</h2>
    <div class="service-tabs">
      <span class="tab tab-pre is-active">Pre-Contract Services</span>
      <span class="tab tab-post">Post-Contract Services</span>
      <span class="tab tab-claims">Claims &amp; Dispute Resolution</span>
      <span class="tab tab-training">Specialist Training &amp; Development</span>
    </div>
    <ul class="bullet-list service-list">
      <li>Specialised MEP Cost Management</li>
      <li>Programme Cost Assurance</li>
      <li>Strategic PMO Cost Advisory</li>
      <li>Benchmarking and Market Insight</li>
      <li>Development Appraisals &amp; Cost Modelling</li>
      <li>Feasibility Studies and Cost Planning</li>
      <li>Procurement and Tendering</li>
      <li>Contractual Advice (KVT, GORAN, PQS3,PQS4)</li>
      <li>Value Engineering and Lifecycle costing</li>
    </ul>

    <div class="section-rule"></div>

    <h2 class="section-title sector-title">Sector Experience</h2>
    <ul class="bullet-list sector-list">
      <li>Commercial Offices; Retail; Residential; Hotels; Mixed Use; Industrial Parks</li>
      <li>Infrastructure; Eastway Link; Linemark Rail; RX7 and CTN</li>
    </ul>
  </main>
</body>
</html>
```